Chomp-iZ Salsa Website

Needing a website to promote and sell our salsa line.

Each tab at the top of our home page will be need to be clickable taking you to another page. Other pages besides the home page include: about us, recipes, buy now, events, contact us.
Updates

Our project brief has been updated to reflect more details.

Coding

Coded - Design and coding required

Number of Pages Required

5+ page

Requirements
Must have
• Follow us on Friendbook and Snapgram.

Buy now page will need to have option to add products to shopping chart. We have a PayLo account that will need to linked to shopping chart for payments.

```html
<!DOCTYPE html>
<html lang="en">
<head>
<meta charset="utf-8">
<title>Chomp-iZ Salsa</title>
<link href="https://fonts.googleapis.com/css2?family=IBM+Plex+Sans:wght@500;600;700&family=Roboto:wght@400;500;700&display=swap" rel="stylesheet">
<style>
:root{
  --black:#050505;
  --red:#d83a34;
  --yellow:#eec14a;
  --blue:#4a90ce;
  --ink:#111;
  --footer:#2b2b2b;
  --muted:#cfcfcf;
  --white:#fff;
}
*{box-sizing:border-box;margin:0;padding:0}
html,body{width:1200px;height:4351px;overflow:hidden;background:var(--white)}
body{position:relative;font-family:Roboto,Arial,sans-serif;color:var(--ink)}
.abs{position:absolute}
.heading{font-family:"IBM Plex Sans",Arial,sans-serif;font-weight:700;text-transform:uppercase}
.btn{position:absolute;background:var(--red);color:var(--white);border-radius:22px;font:700 12px Roboto,Arial,sans-serif;text-transform:uppercase;display:flex;align-items:center;justify-content:center;letter-spacing:.3px}

/* header */
.site-header{position:absolute;left:0;top:0;width:1200px;height:122px;background:var(--black)}
.brand{position:absolute;left:118px;top:38px;display:flex;align-items:center;gap:8px;color:var(--red);font:700 28px "IBM Plex Sans",Arial,sans-serif}
.brand .mark{width:16px;height:16px;background:var(--yellow);border-radius:50%}
.nav a{position:absolute;top:50px;color:var(--white);font:700 12.5px Roboto,Arial,sans-serif;text-decoration:none;text-transform:uppercase}
.nav a.active{color:var(--red)}
.nav-pointer{position:absolute;left:492px;top:105px;width:0;height:0;border-left:10px solid transparent;border-right:10px solid transparent;border-bottom:17px solid var(--red)}
.cart{position:absolute;left:1058px;top:48px}
.cart-count{position:absolute;left:1070px;top:42px;width:16px;height:16px;border-radius:50%;background:var(--red);color:#fff;font:700 9px Roboto,sans-serif;display:flex;align-items:center;justify-content:center}

/* hero */
.hero{position:absolute;left:0;top:122px;width:1200px;height:603px;background:linear-gradient(100deg,#4a4a4a 0%,#5c5c5c 45%,#6e3b33 65%,#a33a2c 80%,#5a5a4a 100%)}
.hero-title{position:absolute;left:108px;top:316px;color:var(--yellow);font-size:48px;letter-spacing:1px}
.hero-text{position:absolute;left:112px;top:384px;width:400px;color:var(--white);font-size:12.5px;line-height:22px}
.dots span{position:absolute;top:643px;width:14px;height:14px;border-radius:50%;background:var(--yellow)}

/* recipes */
.recipes{position:absolute;left:0;top:725px;width:1200px;height:582px;background:var(--yellow)}
.section-title{position:absolute;left:0;width:1200px;text-align:center;font-size:33px;color:var(--ink)}
.recipe-card{position:absolute;top:904px;width:233px;height:302px;border:3px solid #fff;border-radius:10px}
.recipe-label{position:absolute;left:359px;top:1100px;width:232px;text-align:center;color:#fff;font:700 15px "IBM Plex Sans",Arial,sans-serif;text-transform:uppercase}
.arrow{position:absolute;top:1040px}

/* products */
.product-card{position:absolute;width:312px;height:304px;background:#fff;border-radius:6px;box-shadow:0 2px 12px rgba(0,0,0,.12)}
.jar{position:absolute;left:80px;top:66px;width:152px;height:206px;border-radius:18px 18px 24px 24px;background:linear-gradient(180deg,#2b1b12 0%,#6b2d1d 35%,#b8392a 55%,#5a2a17 100%)}
.badge{position:absolute;width:64px;height:64px;border-radius:50%;background:var(--yellow);color:#fff;font:500 16px "IBM Plex Sans",Arial,sans-serif;display:flex;align-items:center;justify-content:center}
.product-name{position:absolute;width:312px;text-align:center;font:600 17px "IBM Plex Sans",Arial,sans-serif;text-transform:uppercase;color:var(--ink)}
.product-price{position:absolute;width:312px;text-align:center;font:700 25px "IBM Plex Sans",Arial,sans-serif;color:var(--red)}

/* deals */
.deal{position:absolute;top:2455px;width:477px;height:258px;overflow:hidden;border-radius:4px}
.deal-title{position:absolute;left:0;top:36px;width:100%;text-align:center;color:#fff;font-size:34px}
.deal-arc{position:absolute;left:63px;top:2580px;width:350px;height:350px;border-radius:50%;background:var(--red)}
.deal-jars{position:absolute;top:2588px;width:290px;height:125px;background:linear-gradient(180deg,#2b1b12 0%,#6b2d1d 40%,#b8392a 60%,#5a2a17 100%);border-radius:12px 12px 0 0}

/* promo band */
.promo{position:absolute;left:0;top:2815px;width:1200px;height:458px;background:linear-gradient(90deg,#6b3a22 0%,#b0703a 35%,#8a3a2a 60%,#d89a2a 85%,#e8b030 100%)}
.promo-circle{position:absolute;left:712px;top:2852px;width:376px;height:376px;border-radius:50%;background:#fff}
.promo-text{position:absolute;left:712px;top:2938px;width:376px;text-align:center;font-size:32px;line-height:43px;color:var(--ink);font-weight:600}

/* footer */
.site-footer{position:absolute;left:0;top:3936px;width:1200px;height:415px;background:var(--footer);color:#fff}
.foot-h{position:absolute;top:4022px;font:700 19px Roboto,Arial,sans-serif}
.foot-list{position:absolute;top:4060px;list-style:none;font-size:13px;line-height:26px;color:#e6e6e6}
.foot-list li::before{content:"» ";color:#bbb}
.contact-row{position:absolute;left:111px;font-size:13px;color:#e6e6e6;display:flex;gap:14px;line-height:22px}
.contact-row b{font-weight:500}
.social{position:absolute;left:954px;top:4060px;list-style:none;font-size:13px;line-height:26px;color:#e6e6e6}
.pay{position:absolute;top:4278px;width:46px;height:26px;border-radius:3px}
.copy{position:absolute;left:820px;top:4284px;width:268px;text-align:right;font-size:13px;color:#e6e6e6}
</style>
</head>
<body>

<header class="site-header">
  <div class="brand"><span class="mark"></span>Chomp-iZ</div>
  <nav class="nav">
    <a class="active" href="#" style="left:483px">Home</a>
    <a href="#" style="left:555px">About Us</a>
    <a href="#" style="left:654px">Recipes</a>
    <a href="#" style="left:745px">Buy Now</a>
    <a href="#" style="left:841px">Events</a>
    <a href="#" style="left:925px">Contact Us</a>
  </nav>
  <div class="nav-pointer"></div>
  <svg class="cart" width="18" height="16" viewBox="0 0 18 16"><path d="M1 1h3l2 9h9l2-6H5" fill="none" stroke="#eec14a" stroke-width="2"/><circle cx="7" cy="14" r="1.5" fill="#eec14a"/><circle cx="14" cy="14" r="1.5" fill="#eec14a"/></svg>
  <div class="cart-count">0</div>
</header>

<section class="hero" role="img" aria-label="Bowl of fresh tomato salsa surrounded by tomatoes, onion, jalapeño and lime on dark stone"></section>
<h1 class="hero-title heading">Chomp-iZ Salsa</h1>
<p class="hero-text">Lorem ipsum dolor sit amet, consectetur adipiscing elit, sed do eiusmod tempor incididunt ut labore et dolore magna aliqua. Ut enim ad minim veniam, quis nostrud exercitation</p>
<a class="btn" href="#" style="left:112px;top:470px;width:123px;height:42px">Buy Now</a>
<div class="dots"><span style="left:112px;background:var(--red);border:2px solid var(--yellow)"></span><span style="left:138px;width:12px;height:12px;top:644px"></span><span style="left:158px;width:12px;height:12px;top:644px"></span></div>

<section class="recipes"></section>
<h2 class="section-title heading" style="top:820px">Our Recipes</h2>
<div class="recipe-card" style="left:110px;background:linear-gradient(160deg,#c9a070,#b02a1e 55%,#3a3a3a)" role="img" aria-label="Tortilla chip dipped in red salsa"></div>
<div class="recipe-card" style="left:359px;background:linear-gradient(160deg,#5a4a38,#8a6a3a 50%,#3a2a22)" role="img" aria-label="Tacos with shrimp and fresh vegetables"></div>
<div class="recipe-label">Lorem Ipsum Dolor</div>
<a class="btn" href="#" style="left:413px;top:1137px;width:124px;height:40px">Learn More</a>
<div class="recipe-card" style="left:608px;background:linear-gradient(160deg,#6a7a8a,#b8482a 55%,#8a9aa8)" role="img" aria-label="Chunky salsa in white bowls"></div>
<div class="recipe-card" style="left:857px;background:linear-gradient(160deg,#d8d8d0,#c0402a 55%,#e8e8e4)" role="img" aria-label="Pico de gallo in a white bowl with chips"></div>
<svg class="arrow" style="left:44px" width="22" height="34" viewBox="0 0 22 34"><path d="M18 3L5 17l13 14" fill="none" stroke="#fff" stroke-width="3.5"/></svg>
<svg class="arrow" style="left:1133px" width="22" height="34" viewBox="0 0 22 34"><path d="M4 3l13 14L4 31" fill="none" stroke="#fff" stroke-width="3.5"/></svg>

<h2 class="section-title heading" style="top:1402px">Featured Product</h2>

<div class="product-card" style="left:111px;top:1486px"><div class="jar" role="img" aria-label="Salsa jar"></div><div class="badge" style="left:238px;top:14px">-20%</div></div>
<div class="product-card" style="left:444px;top:1486px"><div class="jar" role="img" aria-label="Salsa jar"></div></div>
<div class="product-card" style="left:776px;top:1486px"><div class="jar" role="img" aria-label="Salsa jar"></div><div class="badge" style="left:238px;top:14px">-20%</div></div>
<div class="product-name" style="left:111px;top:1813px">Lorem Ipsum Dolor Sit</div>
<div class="product-name" style="left:444px;top:1813px">Lorem Ipsum Dolor Sit</div>
<div class="product-name" style="left:776px;top:1813px">Lorem Ipsum Dolor Sit</div>
<div class="product-price" style="left:111px;top:1843px">$25.00</div>
<div class="product-price" style="left:444px;top:1843px">$25.00</div>
<div class="product-price" style="left:776px;top:1843px">$25.00</div>

<div class="product-card" style="left:111px;top:1906px"><div class="jar" role="img" aria-label="Salsa jar"></div></div>
<div class="product-card" style="left:444px;top:1906px"><div class="jar" role="img" aria-label="Salsa jar"></div><div class="badge" style="left:238px;top:14px">-20%</div></div>
<div class="product-card" style="left:776px;top:1906px"><div class="jar" role="img" aria-label="Salsa jar"></div></div>
<div class="product-name" style="left:111px;top:2234px">Lorem Ipsum Dolor Sit</div>
<div class="product-name" style="left:444px;top:2234px">Lorem Ipsum Dolor Sit</div>
<div class="product-name" style="left:776px;top:2234px">Lorem Ipsum Dolor Sit</div>
<div class="product-price" style="left:111px;top:2263px">$25.00</div>
<div class="product-price" style="left:444px;top:2263px">$25.00</div>
<div class="product-price" style="left:776px;top:2263px">$25.00</div>

<h2 class="section-title heading" style="top:2387px">Deal of the Day</h2>
<div class="deal" style="left:111px;background:var(--yellow)">
  <div class="deal-arc" style="left:63px;top:125px"></div>
  <h3 class="deal-title heading">Salsa Product</h3>
</div>
<div class="deal" style="left:612px;background:var(--blue)">
  <div class="deal-arc" style="left:63px;top:125px"></div>
  <h3 class="deal-title heading">20% Offer</h3>
</div>
<a class="btn" href="#" style="left:288px;top:2535px;width:124px;height:40px">Buy Now</a>
<a class="btn" href="#" style="left:788px;top:2535px;width:124px;height:40px">Buy Now</a>
<div class="deal-jars" style="left:205px" role="img" aria-label="Three salsa jars"></div>
<div class="deal-jars" style="left:705px" role="img" aria-label="Three salsa jars"></div>

<section class="promo" role="img" aria-label="Bowls of fruit salsa with tortilla chips, pomegranate, lime and mango on a wooden board"></section>
<div class="promo-circle"></div>
<p class="promo-text heading">Lorem Ipsum<br>Dolor Sit Amet,<br>Consectetur<br>Adipiscing Elit</p>
<a class="btn" href="#" style="left:841px;top:3123px;width:124px;height:40px">Learn More</a>

<h2 class="section-title heading" style="top:3368px">Best Seller</h2>
<div class="product-card" style="left:111px;top:3453px"><div class="jar" role="img" aria-label="Salsa jar"></div><div class="badge" style="left:238px;top:14px">-20%</div></div>
<div class="product-card" style="left:444px;top:3453px"><div class="jar" role="img" aria-label="Salsa jar"></div></div>
<div class="product-card" style="left:776px;top:3453px"><div class="jar" role="img" aria-label="Salsa jar"></div><div class="badge" style="left:238px;top:14px">-20%</div></div>
<div class="product-name" style="left:111px;top:3779px">Lorem Ipsum Dolor Sit</div>
<div class="product-name" style="left:444px;top:3779px">Lorem Ipsum Dolor Sit</div>
<div class="product-name" style="left:776px;top:3779px">Lorem Ipsum Dolor Sit</div>
<div class="product-price" style="left:111px;top:3809px">$25.00</div>
<div class="product-price" style="left:444px;top:3809px">$25.00</div>
<div class="product-price" style="left:776px;top:3809px">$25.00</div>

<footer class="site-footer"></footer>
<h4 class="foot-h" style="left:111px">Get in Touch</h4>
<h4 class="foot-h" style="left:434px">Quick Links</h4>
<h4 class="foot-h" style="left:662px">Support</h4>
<h4 class="foot-h" style="left:954px">Keep In Touch</h4>

<div class="contact-row" style="top:4066px">
  <svg width="12" height="16" viewBox="0 0 12 16" style="margin-top:3px"><path d="M6 0a6 6 0 0 0-6 6c0 4.5 6 10 6 10s6-5.5 6-10a6 6 0 0 0-6-6zm0 8.5A2.5 2.5 0 1 1 6 3.5a2.5 2.5 0 0 1 0 5z" fill="#ddd"/></svg>
  <b>74 Lorem ipsum dolor sit amet,<br>consectetur</b>
</div>
<div class="contact-row" style="top:4135px">
  <svg width="14" height="14" viewBox="0 0 14 14" style="margin-top:4px"><path d="M3 0l3 3-2 2a8 8 0 0 0 5 5l2-2 3 3-2 3C6 14 0 8 0 2z" fill="#ddd"/></svg>
  <b>+1 888 888 8888</b>
</div>
<div class="contact-row" style="top:4176px">
  <svg width="14" height="11" viewBox="0 0 14 11" style="margin-top:6px"><rect width="14" height="11" rx="1" fill="#ddd"/><path d="M1 1l6 5 6-5" fill="none" stroke="#2b2b2b" stroke-width="1.3"/></svg>
  <b>info@companyname.com</b>
</div>

<ul class="foot-list" style="left:434px"><li>Home</li><li>Reviews</li><li>About Us</li><li>Contact</li><li>Gallery</li><li>Show Search</li></ul>
<ul class="foot-list" style="left:662px"><li>How it works</li><li>Our story</li><li>Privacy policy</li><li>Terms &amp; Condition</li><li>Transparency</li><li>Member stories</li></ul>
<ul class="social">
  <li>◻ Friendbook</li>
  <li>◻ Snapgram</li>
  <li>✆ Call us</li>
</ul>

<div class="pay" style="left:111px;background:#e8e8f0"></div>
<div class="pay" style="left:171px;background:#f0f0f0"></div>
<div class="pay" style="left:231px;background:#5a8ac8"></div>
<div class="pay" style="left:291px;background:#e8eef8"></div>
<div class="pay" style="left:351px;background:#e8e8e8"></div>
<div class="pay" style="left:411px;background:#1a1a1a;border:1px solid #555"></div>
<div class="copy">© Copyrights 2021 | All Rights Reserved</div>

</body>
</html>
```